Lumbra Deckworks Company (southern african focus for now) needs a e-commerce website

We need a website design for a playing card company based in Southern Africa/United States. We make locally-sourced playing cards (standard 52 card deck, with customized fronts and backs) for everyone and collaborate with local artists to uplift their talents, while celebrating their nation's culture, heritage, beauty and identity. We would like to see designs that use the colours blue (see flag of Eswatini as starting product), white and some red accents (or your recommendation). The final design should communicate elegance, fun and sustainable prosperity.

Target Market(s)

Everyone loves playing cards. From the solo adventurer to the party host, first time learner or expert, young, middle and old, we need to attract a broad audience that appreciates the finer things and supports sustainable, environmentally contentiousness causes that support the local economy and uplift local talent - thing global, act local.

Number of Pages Required

4 page

Font styles to use
Serif
Sans Serif

Requirements
Must have
• Pages to include Home (Main), About (Our Story), Shop and Contact
Nice to have
• While designs may be static, elements of graceful movement would be desirable. Perhaps functionality of scrolling down on homepage showing playing cards in use, front and back. Quindle and Zorvax store's capture that elegant yet rich look.
Should not have
• Too many products. We focus on 1-2.

```html
<!DOCTYPE html>
<html lang="en">
<head>
<meta charset="utf-8">
<title>Lumbra – About</title>
<link rel="stylesheet" href="https://fonts.googleapis.com/css2?family=Poppins:wght@400;500&family=Noto+Serif:wght@400&display=swap">
<style>
:root{
  --bar:#333333;
  --page:#f3f3f3;
  --ink:#111111;
  --white:#ffffff;
  --accent:#d0141b;
  --flag-blue:#4a6fc9;
  --flag-red:#b8262c;
  --muted:#d8d8d8;
}
*{margin:0;padding:0;box-sizing:border-box}
html,body{width:1010px;height:1200px;overflow:hidden}
body{background:var(--page);font-family:"Poppins",sans-serif;color:var(--ink);position:relative}
.topbar{position:absolute;left:0;top:0;width:1010px;height:88px;background:var(--bar)}
.brand{position:absolute;left:74px;top:30px;display:flex;align-items:center;gap:8px;color:var(--white);font-family:"Noto Serif",serif;font-size:21px}
.brand-dot{width:18px;height:18px;border-radius:50%;background:var(--white)}
.nav{position:absolute;top:37px;left:0;font-size:13.3px;color:var(--white)}
.nav a{position:absolute;color:var(--white);text-decoration:none;white-space:nowrap}
.nav .current{border-bottom:1.5px solid var(--white);padding:0 3px 2px}
.contact-btn{position:absolute;left:836px;top:32px;width:100px;height:34px;border:1.5px solid var(--white);color:var(--white);font-size:13.3px;display:flex;align-items:center;justify-content:center}
.headline{position:absolute;left:0;top:140px;width:1010px;text-align:center;font-weight:500;font-size:35.5px;line-height:44.5px}
.headline .accent{color:var(--accent)}
.copy{position:absolute;font-size:17.7px;line-height:26.6px}
.copy p+p{margin-top:32px}
.art{position:absolute}
.footer{position:absolute;left:0;top:1067px;width:1010px;height:133px;background:var(--bar);color:var(--white)}
.footer-brand{position:absolute;left:56px;top:40px;display:flex;align-items:center;gap:14px;font-family:"Noto Serif",serif;font-size:35px}
.footer-brand .brand-dot{width:36px;height:36px}
.foot-col{position:absolute;font-size:10.5px;line-height:24px}
.foot-contact li{list-style:none;display:flex;align-items:center;gap:8px}
.social{position:absolute;left:698px;top:30px;display:flex;gap:26px}
.social span{width:40px;height:40px;border:2px solid var(--white);border-radius:50%;display:flex;align-items:center;justify-content:center;font-size:9px}
.legal{position:absolute;left:698px;top:1145px;font-size:9px;color:var(--white)}
</style>
</head>
<body>
<header class="topbar">
  <div class="brand"><span class="brand-dot"></span>Lumbra</div>
  <nav class="nav">
    <a style="left:293px">Home</a>
    <a class="current" style="left:377px">About</a>
    <a style="left:467px">Collections</a>
    <a style="left:589px">Blog</a>
  </nav>
  <div class="contact-btn">Contact</div>
</header>

<h1 class="headline">We’re celebrating cultural heritage and local<br>artistic talent through playing cards<br><span class="accent">one card at a time.</span></h1>

<div class="copy" style="left:147px;top:416px;width:340px">
  <p>We’re environmentally sustainable, philanthropic, and doing this for the good of the country. It’s about celebrating our heritage, whilst celebrating our diversity</p>
</div>

<div class="art" role="img" aria-label="Fanned playing cards with red, blue and yellow flag-inspired backs beside their card box" style="left:552px;top:347px;width:440px;height:260px;border-radius:12px;background:linear-gradient(120deg,var(--flag-blue) 0%,var(--flag-red) 35%,var(--flag-red) 65%,var(--flag-blue) 100%);opacity:.9"></div>

<div class="art" role="img" aria-label="Playing cards tumbling through the air, showing flag-inspired backs and white faces with clubs, hearts and spades" style="left:0;top:580px;width:466px;height:430px;background:radial-gradient(ellipse at 40% 50%,var(--flag-red) 0%,var(--flag-blue) 45%,var(--white) 75%,var(--page) 100%)"></div>

<div class="copy" style="left:512px;top:715px;width:350px">
  <p>Lorem ipsum dolor sit amet, consectetur adipiscing elit. Dapibus mauris ac, mauris egestas. Porta faucibus aenean leo varius id eros sed pharetra.</p>
  <p>Lorem ipsum dolor sit amet, consectetur adipiscing elit. Dapibus mauris ac, mauris egestas.</p>
</div>

<footer class="footer">
  <div class="footer-brand"><span class="brand-dot"></span>Lumbra</div>
  <ul class="foot-col" style="left:383px;top:26px;list-style:none">
    <li>Corporate office</li><li>International Branch</li><li>Contact Us</li>
  </ul>
  <ul class="foot-col foot-contact" style="left:506px;top:26px">
    <li><svg width="12" height="12" viewBox="0 0 12 12" fill="none" stroke="#fff" stroke-width="1.2"><path d="M3 1.5h2l1 2.5-1.3 1a6 6 0 0 0 2.3 2.3l1-1.3 2.5 1v2a1 1 0 0 1-1 1A8.5 8.5 0 0 1 2 2.5a1 1 0 0 1 1-1z"/></svg>+268 7000 1234</li>
    <li><svg width="12" height="12" viewBox="0 0 12 12" fill="none" stroke="#fff" stroke-width="1.2"><path d="M3 1.5h2l1 2.5-1.3 1a6 6 0 0 0 2.3 2.3l1-1.3 2.5 1v2a1 1 0 0 1-1 1A8.5 8.5 0 0 1 2 2.5a1 1 0 0 1 1-1z"/></svg>+268 7000 1234</li>
    <li><svg width="13" height="11" viewBox="0 0 13 11" fill="none" stroke="#fff" stroke-width="1.2"><rect x="0.8" y="0.8" width="11.4" height="9.4"/><path d="M1 1l5.5 5 5.5-5"/></svg>hello@lumbradeck.com</li>
  </ul>
  <div class="social"><span>Pixo</span><span>Chirr</span><span>Linko</span><span>Snapa</span></div>
</footer>
<div class="legal">© All Rights Reserved. Lumbra. 2020</div>
</body>
</html>
```